Building company buisness cards

We are looking for a sharp modern new look for our business cards.We are a New Zealand based company that specialises in house and land packages.We have attached a photo of the current logo and would like to see if it can be improved somehow if needed.We are open to any colours but we have chosen Black and White at this stage. Feel free to change the font and make the logo smarter looking.Play with the colours and see what looks best.We want a card that looks so good know one will want to throw it away!

Target Market(s)

Building profesonals, home buyers

Industry/Entity Type

Building

Contact Information for Business Card

Garrick Tenwood
0275390628
garrickt@hartvale.co.nz

Font styles to use
Serif
Sans Serif

Colors

Designer to choose colors to be used in the design.

Requirements
Must have
• Just the logo on one side and details on the other
• Clean simple looking card
Nice to have
• Round corners and detail like raised or spot UV
• Something that stands out
Should not have
• To title needed, Director etc

```html
<!DOCTYPE html>
<html lang="en">
<head>
<meta charset="utf-8">
<title>Hartvale Business Cards</title>
<link href="https://fonts.googleapis.com/css2?family=Crimson+Pro:wght@400;700&family=Roboto:wght@400&display=swap" rel="stylesheet">
<style>
  :root {
    --backdrop: #e3e3e3;
    --card-white: #ffffff;
    --ink: #0b0c10;
    --ink-soft: #3d3d3d;
    --paper-text: #ffffff;
  }
  * { margin: 0; padding: 0; box-sizing: border-box; }
  html, body {
    width: 1125px; height: 1200px; overflow: hidden;
    background: var(--backdrop);
  }
  .canvas { position: relative; width: 1125px; height: 1200px; }

  .card {
    position: absolute; left: 166px; width: 800px; height: 455px;
    border-radius: 24px; overflow: hidden;
  }
  .card--front { top: 103px; background: var(--card-white); }
  .card--back  { top: 620px; background: var(--ink); }

  .brand-band {
    position: absolute; left: 0; top: 80px; width: 380px; height: 72px;
    background: var(--ink);
  }
  .brand-name {
    position: absolute; left: 398px; top: 60px;
    font-family: "Crimson Pro", serif; font-weight: 700;
    font-size: 90px; line-height: 100px; color: var(--ink);
    letter-spacing: -1px;
  }
  .brand-dot {
    position: absolute; left: 724px; top: 96px;
    width: 40px; height: 40px; border-radius: 50%; background: var(--ink);
  }

  .holder-name {
    position: absolute; left: 54px; top: 286px;
    font-family: "Crimson Pro", serif; font-weight: 700;
    font-size: 30px; letter-spacing: 0.5px; color: var(--ink);
    text-transform: uppercase;
  }
  .contact-list { position: absolute; left: 55px; top: 340px; list-style: none; }
  .contact-item {
    display: flex; align-items: center; gap: 9px; height: 27px;
    font-family: "Crimson Pro", serif; font-size: 19px; color: var(--ink-soft);
  }
  .contact-item svg { width: 18px; height: 18px; fill: var(--ink); }

  .web-front {
    position: absolute; right: 50px; top: 368px;
    font-family: "Crimson Pro", serif; font-size: 20px; letter-spacing: 1px;
    color: var(--ink-soft);
  }
  .web-front strong { color: var(--ink); font-weight: 700; }

  .back-brand {
    position: absolute; left: 0; right: 0; top: 170px;
    display: flex; justify-content: center; align-items: center; gap: 22px;
  }
  .back-brand__name {
    font-family: "Crimson Pro", serif; font-weight: 700;
    font-size: 84px; line-height: 90px; color: var(--paper-text);
  }
  .back-brand__dot { width: 36px; height: 36px; border-radius: 50%; background: var(--paper-text); }
  .web-back {
    position: absolute; left: 0; right: 0; top: 388px; text-align: center;
    font-family: "Roboto", sans-serif; font-size: 19px; letter-spacing: 8.5px;
    color: var(--paper-text);
  }
</style>
</head>
<body>
<main class="canvas">
  <section class="card card--front">
    <div class="brand-band"></div>
    <div class="brand-name">Hartvale</div>
    <div class="brand-dot"></div>

    <h1 class="holder-name">Garrick Tenwood</h1>
    <ul class="contact-list">
      <li class="contact-item">
        <svg viewBox="0 0 24 24" aria-hidden="true"><path d="M6.6 10.8a15.1 15.1 0 0 0 6.6 6.6l2.2-2.2a1 1 0 0 1 1-.25 11.4 11.4 0 0 0 3.6.57 1 1 0 0 1 1 1V20a1 1 0 0 1-1 1A17 17 0 0 1 3 4a1 1 0 0 1 1-1h3.5a1 1 0 0 1 1 1c0 1.25.2 2.45.57 3.57a1 1 0 0 1-.25 1z"/></svg>
        <span>0275390628</span>
      </li>
      <li class="contact-item">
        <svg viewBox="0 0 24 24" aria-hidden="true"><path d="M2 5h20v14H2zm2 2v.4l8 5.2 8-5.2V7zm0 2.8V17h16V9.8l-8 5.2z"/></svg>
        <span>garrickt@hartvale.co.nz</span>
      </li>
    </ul>
    <div class="web-front">www.<strong>HARTVALE</strong>.co.nz</div>
  </section>

  <section class="card card--back">
    <div class="back-brand">
      <span class="back-brand__name">Hartvale</span>
      <span class="back-brand__dot"></span>
    </div>
    <div class="web-back">www.Hartvale.co.nz</div>
  </section>
</main>
</body>
</html>
```